Verodex business card

Business card for sustainable investment company called "Verodex". Verodex is an exchange platform selling carbon credits between buyers and sellers. Carbon Credits are an environmental commodity for reducing global carbon emissions.

the card should obviously have our logo and the theme should be sustainability/environment mixed with a trading platform.

Contact Information for Business Card

Logo, Name, Title, Phone, Email

Colors
0054AA
0677BA
7BADD7
CADEEF
E8F1F8
0094D4
00A9DD
6FCCEA
C7EBF8
E9F6FB
00AB8E
00BBA5
67D7C9
C6EFE9
E9F9F6
59FF00
82FF00
B8FF75
E3FFCB
F4FFEA

```html
<!DOCTYPE html>
<html lang="en">
<head>
<meta charset="utf-8">
<title>Verodex business card</title>
<link href="https://fonts.googleapis.com/css2?family=Montserrat:wght@400;500;700;800&display=swap" rel="stylesheet">
<style>
  :root{
    --page:#e9edf1;
    --paper:#ffffff;
    --ink:#16243f;
    --navy:#1a2b5c;
    --navy-deep:#0f1a3d;
    --band-start:#35b8ec;
    --band-end:#4a7ec6;
    --accent:#00a9dd;
    --white:#ffffff;
  }
  *{box-sizing:border-box;margin:0;padding:0}
  html,body{width:1200px;height:786px;overflow:hidden}
  body{
    background:var(--page);
    font-family:"Montserrat",sans-serif;
    display:flex;align-items:center;justify-content:center;gap:40px;
  }
  .card{
    width:540px;height:309px;position:relative;overflow:hidden;
    border-radius:4px;box-shadow:0 10px 30px rgba(20,30,60,.18);
  }
  .card-front{background:var(--paper)}
  .brand{
    position:absolute;left:44px;top:46px;
    display:flex;align-items:center;gap:18px;
  }
  .brand-mark{width:46px;height:46px;background:var(--accent);border-radius:6px}
  .brand-name{
    font-weight:800;font-size:46px;letter-spacing:1px;color:var(--navy);
    text-transform:uppercase;line-height:1;
  }
  .band{
    position:absolute;left:0;right:0;top:136px;height:112px;
    background:linear-gradient(90deg,var(--band-start),var(--band-end));
    display:flex;align-items:center;
  }
  .person{width:250px;padding-left:40px;text-align:right;padding-right:22px}
  .person-name{font-weight:800;font-size:22px;color:var(--white);line-height:1.1}
  .person-title{font-weight:500;font-size:11px;color:var(--white);letter-spacing:.5px;margin-top:3px}
  .divider{width:1px;height:58px;background:rgba(255,255,255,.55)}
  .contacts{list-style:none;padding-left:22px}
  .contacts li{display:flex;align-items:center;gap:9px;font-size:11.5px;color:var(--white);line-height:1.55}
  .contacts svg{width:10px;height:10px;flex:none}
  .address{
    position:absolute;left:0;right:0;top:262px;text-align:center;
    font-size:12px;font-weight:500;color:var(--ink);
  }
  .card-back{
    background:linear-gradient(135deg,#4f6fb4 0%,#2a3f86 45%,var(--navy-deep) 100%);
  }
  .back-pattern{position:absolute;inset:0}
  .back-mark{
    position:absolute;right:40px;top:90px;width:30px;height:30px;
    background:var(--accent);border-radius:4px;
  }
</style>
</head>
<body>
  <section class="card card-front">
    <div class="brand">
      <span class="brand-mark"></span>
      <span class="brand-name">Verodex</span>
    </div>
    <div class="band">
      <div class="person">
        <p class="person-name">Maren Castell</p>
        <p class="person-title">CEO &amp; Founder</p>
      </div>
      <div class="divider"></div>
      <ul class="contacts">
        <li>
          <svg viewBox="0 0 10 10"><path d="M2 1h2l1 2.3-1.2.9a5 5 0 0 0 2 2l.9-1.2L9 6v2a1 1 0 0 1-1 1A7 7 0 0 1 1 2a1 1 0 0 1 1-1z" fill="#fff"/></svg>
          (37) 555-0182
        </li>
        <li>
          <svg viewBox="0 0 10 10"><rect x="0.5" y="2" width="9" height="6.5" rx="1" fill="#fff"/><path d="M1 2.6l4 3 4-3" stroke="#4a8ed0" stroke-width=".9" fill="none"/></svg>
          info@verodex.com
        </li>
        <li>
          <svg viewBox="0 0 10 10"><circle cx="5" cy="5" r="4.3" fill="none" stroke="#fff" stroke-width="1"/><path d="M.8 5h8.4M5 .7c-2.2 2.5-2.2 6.1 0 8.6M5 .7c2.2 2.5 2.2 6.1 0 8.6" stroke="#fff" stroke-width=".8" fill="none"/></svg>
          www.verodex.com
        </li>
      </ul>
    </div>
    <p class="address">48 Harbor Lane, Suite 210, Linford, PA 19022</p>
  </section>

  <section class="card card-back">
    <div class="back-pattern" role="img" aria-label="Repeating pattern of the Verodex brand symbol in glossy navy tones"></div>
    <span class="back-mark"></span>
  </section>
</body>
</html>
```